COMPANY NAME: Bright Harbor Ventures: Task Description: We are a new UK based business with global rea

Target Market

- Personal and professional development – 30-55 age group, corporate leaders, Eastern European and Asian markets
- On-assignment projects – Corporate market – Eastern European and Asian Markets
- Property investment - 35-65 age group, Europe, USA, Australia

What we need

We need logos and brand design for a suite of web platforms (website, twitter and Facebook profile). We would like to have a cohesive and consistent look across all of our online platforms. The design suite must therefore include social media logos, backgrounds and headers. Specifically we are looking for:

a. Facebook header/page design: likely to have a more youthful look

b. Website: Header, background and layout that is responsive to devices, iPhone primarily, then tablet, then PC (we have purchased a website building package from SiteKettle so if you are familiar with one of their themes, it would be great to have a design that fits with a theme you would recommend); Design should be able to accommodate a place to position video in the medium term but an image in the short term.

c. LinkedIn: header/logo; more corporate look

d. Twitter: background/logo

e. Powerpoint template: background and logo - simple and soft background not busy

f. Electronic Newsletter: logo, header and sidebar; simple and soft background not busy

h. Business card: sophisticated and simple

Colors

We have in mind a preference for colors from the purple family, maybe lavender, so as to appeal to all genders and age groups. Though we are happy to go with a recommendation if you think otherwise.

We would like a look that is professional, airy, bright, fresh, futuristic, insightful, friendly.

Ethos of the brand

- experiencing opportunity and being fulfilled in a changing world
- services are facilitated through insights
- support provided through our product, services and tailored approach to coaching/partnerships (which includes private client match-making)
- we are service providers and passionate about quality and modern leadership skills at all stages in life.

The company name is "Bright Harbor Ventures” - our main message is helping people move to the next level - through investments, personal and professional growth.

Some of our messaging

1. International Leadership in a new world.

2. New technology;

3. Informed;

4. Positively Influential

5. Making a difference;

6. Empowered;

7. Risk free investments;

8. Commercial opportunity;

9. Fulfilled living;

10. Carefree and Fun Living;

11. Progression;

12. Open-minded

13. Energy/dynamic

The Business:
The business is to move people very quickly out of situations that hold them back. the situations could be their own personal situations; their career; their jobs; their teams; their ideas; their finances; their financial opportunities. Remove their fears and give them the strategies to take action. The team are international and have 40 years experience between them in this area.

We do want to come across modern and dynamic, customer outcome focussed, building long-term relationships; international.
Updates

Project Deadline Extended
Reason: We have not found the right designs - we are not just looking for a website design but also images and logos. Most images we can see in the designs are stock images - very standard. We need an image which will be the face of the company, like the shop front window. This main image will be used on social media (top image) and also the home page of the website.

Target Market(s)

30-55 years
Eastern Europe; UK; Asia; Africa; Middle East
Personal, Professional, Corporate, and Financial Growth

Industry/Entity Type

Business Service

Contact Information for Business Card

Simple and stylish
the 3 areas of the business on the reverse -

International look - Offices in UK and San Francisco

Company name
web address www.brightharborventure.com
email director@brightharborventure.com
Facebook bright harbor venture
LinkedIn Bright Harbor Venture
Twitter Bright Harbor Venture
Telephone: +44 (0) 768 213 5597

Logo Text

Something that symbolises unlimited growth - probably not text - could use the word INSIGHT in some way

Number of Pages Required

1 page

Colors
e4daeb
f3f1f8
ffffff

Requirements
Must have
• social media symbols and address
• company name
• Melanie Thorpe
• Director
• Telephone +44 (0) 768 213 5597
• Website name www.brightharborventure.co.uk
• Reverse of Card:
• Discreet, Fast, Bright Harbor Consultancy
• Corporate, Professional, Personal & Property Investment
Nice to have
• not too angular; soft lines; not too cluttered (possibly social media on the reverse and just logo, name, number on the front?
Should not have
• too busy

```html
<!DOCTYPE html>
<html lang="en">
<head>
<meta charset="utf-8">
<title>Bright Harbor Venture</title>
<link href="https://fonts.googleapis.com/css2?family=Roboto:ital,wght@0,400;0,500;0,700;1,400&family=Roboto+Condensed:wght@400;700&display=swap" rel="stylesheet">
<style>
:root{
  --ink:#2d2d33;
  --text:#5b5b63;
  --muted:#7d7d86;
  --accent:#2a9fd6;
  --lavender:#e4daeb;
  --lavender-soft:#f3f1f8;
  --white:#ffffff;
  --dark:#2b2a2e;
  --menu-bg:rgba(20,24,34,.82);
  --plum:#6b3d5c;
  --icon:#55555c;
}
*{box-sizing:border-box;margin:0;padding:0}
html,body{width:1200px;height:2590px;overflow:hidden}
body{position:relative;font-family:'Roboto',sans-serif;color:var(--text);background:var(--white)}
.abs{position:absolute}

/* header + hero */
.hero{left:0;top:0;width:1200px;height:604px;background:linear-gradient(180deg,#1d2b3c 0%,#3a4a5e 35%,#5d6b7b 60%,#2a3340 100%)}
.topbar{left:0;top:0;width:1200px;height:86px;background:rgba(243,241,248,.94)}
.brand{left:97px;top:26px;font:700 28px/34px 'Roboto Condensed',sans-serif;color:var(--ink);letter-spacing:1px}
.menu-btn{left:1007px;top:29px;width:94px;height:33px;border:2px solid var(--plum);border-radius:3px;font:400 15px/29px 'Roboto',sans-serif;color:var(--ink);text-align:center}
.menu-btn span{display:inline-block;width:13px;height:11px;border-top:2px solid var(--ink);border-bottom:2px solid var(--ink);vertical-align:-1px;margin-left:4px;position:relative}
.menu-btn span::after{content:"";position:absolute;left:0;right:0;top:2.5px;border-top:2px solid var(--ink)}
.menu-caret{left:1082px;top:62px;width:0;height:0;border-left:10px solid transparent;border-right:10px solid transparent;border-top:10px solid var(--plum)}
.menu{left:941px;top:86px;width:160px;height:320px;background:var(--menu-bg);list-style:none;padding-top:8px}
.menu li{height:44.5px;padding-left:22px;font:400 12px/44.5px 'Roboto',sans-serif;color:var(--white);border-bottom:1px solid rgba(255,255,255,.08)}
.hero-title{left:97px;top:248px;font:400 38px/44px 'Roboto Condensed',sans-serif;color:var(--white)}
.hero-text{left:97px;top:303px;width:340px;font:400 13.5px/22px 'Roboto',sans-serif;color:var(--white)}
.dots{left:97px;top:389px;display:flex;gap:7px}
.dots i{width:14px;height:14px;border-radius:50%;border:1.5px solid var(--white);display:block}
.dots i.on{background:var(--white)}

/* services */
.services{left:0;top:604px;width:1200px;height:510px;background:linear-gradient(180deg,#f7f7f9,#f1f0f4)}
.section-title{font:400 31px/36px 'Roboto Condensed',sans-serif;color:var(--ink);text-align:center;width:1200px;left:0}
.card{top:713px;width:311px}
.card .photo{height:185px}
.card h3{margin-top:24px;font:400 19px/22px 'Roboto',sans-serif;color:var(--ink)}
.card ul{list-style:none;margin-top:10px}
.card li{font:400 12.5px/21.5px 'Roboto',sans-serif;color:var(--text);padding-left:19px;position:relative}
.card li::before{content:"";position:absolute;left:0;top:6px;width:10px;height:10px;border-radius:50%;background:#555}
.card li::after{content:"";position:absolute;left:3px;top:9px;width:3px;height:3px;border-right:1.5px solid #fff;border-top:1.5px solid #fff;transform:rotate(45deg)}
.btn-outline{display:inline-block;margin-top:14px;border:1px solid #9a9aa2;padding:0 11px;font:400 13px/29px 'Roboto',sans-serif;color:var(--ink);background:var(--white)}

/* welcome */
.welcome{left:0;top:1114px;width:1200px;height:474px;background:linear-gradient(120deg,#ece6f0 0%,#e4daeb 55%,#dccfe4 100%)}
.video{left:98px;top:1203px;width:482px;height:297px;border:4px solid var(--white);background:linear-gradient(135deg,#8fb2c2 0%,#c8d7d9 40%,#6b7e8f 100%)}
.play{left:309px;top:1321px;width:60px;height:60px;border-radius:50%;background:rgba(40,40,45,.75);border:2px solid rgba(255,255,255,.85)}
.play::after{content:"";position:absolute;left:22px;top:16px;border-left:20px solid var(--white);border-top:12px solid transparent;border-bottom:12px solid transparent}
.welcome-title{left:612px;top:1217px;font:700 31px/38px 'Roboto Condensed',sans-serif;color:var(--ink)}
.welcome-text{left:612px;top:1270px;width:490px;font:400 11.5px/19px 'Roboto',sans-serif;color:var(--text)}
.welcome-text p+p{margin-top:12px}
.btn-dark{left:611px;top:1448px;width:123px;height:39px;border:1.5px solid #4a4a52;font:400 12.5px/36px 'Roboto Condensed',sans-serif;color:var(--ink);text-align:center}

/* blog */
.blog-title{left:97px;top:1640px;font:400 29px/34px 'Roboto Condensed',sans-serif;color:var(--ink)}
.arrows{left:1064px;top:1646px;font:400 16px/20px 'Roboto',sans-serif;color:var(--ink);letter-spacing:14px}
.post .thumb{width:187px;height:164px}
.post h4{font:400 15.5px/20px 'Roboto',sans-serif;color:var(--ink);width:270px}
.post .date{margin-top:10px;font:italic 400 13px/18px 'Roboto',sans-serif;color:var(--accent)}
.post .excerpt{margin-top:12px;width:265px;font:400 11.5px/19px 'Roboto',sans-serif;color:var(--text)}
.post .more{margin-top:12px;font:400 12.5px/16px 'Roboto',sans-serif;color:var(--ink)}

/* testimonials */
.testimonials{left:0;top:1946px;width:1200px;height:338px;background:linear-gradient(180deg,#16181e 0%,#23272f 55%,#343a44 80%,#1a1d23 100%)}
.testi-title{top:2010px;color:var(--white)}
.quote{left:212px;top:2072px;width:782px;font:400 12px/19px 'Roboto',sans-serif;color:var(--white);text-align:center}
.quote-mark{left:212px;top:2056px;font:italic 700 26px/26px 'Roboto',sans-serif;color:var(--white)}
.author{left:0;width:1200px;top:2160px;text-align:center;font:italic 400 18px/24px 'Roboto',sans-serif;color:var(--white)}
.author small{font-size:13px}
.bars{left:553px;top:2206px;display:flex;gap:6px}
.bars i{display:block;width:30px;height:3px;background:rgba(255,255,255,.35)}
.bars i.on{background:var(--white)}

/* footer */
.footer{left:0;top:2284px;width:1200px;height:247px;background:var(--lavender)}
.foot-h{top:2318px;font:400 17px/22px 'Roboto Condensed',sans-serif;color:var(--ink)}
.news-text{left:98px;top:2350px;width:215px;font:400 11.5px/19px 'Roboto',sans-serif;color:var(--text)}
.email-field{left:98px;top:2405px;width:244px;height:41px;background:var(--white);font:400 11.5px/41px 'Roboto',sans-serif;color:var(--text);padding-left:14px}
.subscribe{left:98px;top:2457px;width:102px;height:40px;background:var(--dark);color:var(--white);font:500 11.5px/40px 'Roboto',sans-serif;text-align:center}
.contact{left:420px;font:400 12px/19px 'Roboto',sans-serif;color:var(--text);padding-left:27px}
.contact svg{position:absolute;left:0;top:2px}
.links{left:729px;top:2353px;list-style:none}
.links li{font:400 11.5px/22px 'Roboto',sans-serif;color:var(--text)}
.foot-brand{left:890px;top:2344px;width:220px;text-align:center;font:700 29px/32px 'Roboto Condensed',sans-serif;color:var(--ink);letter-spacing:.5px}
.socials{left:936px;top:2428px;display:flex;gap:8px}
.socials span{display:flex;align-items:center;justify-content:center;width:31px;height:31px;border-radius:50%;border:1.5px solid var(--icon)}
.bottom{left:0;top:2531px;width:1200px;height:59px;background:var(--dark);text-align:center;font:400 11.5px/59px 'Roboto',sans-serif;color:#e5e5e8}
</style>
</head>
<body>

<header>
  <div class="abs hero" role="img" aria-label="Business partners shaking hands in front of a city skyline window"></div>
  <div class="abs topbar"></div>
  <div class="abs brand">BRIGHT HARBOR VENTURE</div>
  <div class="abs menu-btn">MENU <span></span></div>
  <div class="abs menu-caret"></div>
  <ul class="abs menu">
    <li>HOME</li><li>ABOUT YOU</li><li>ABOUT US</li><li>OUR VALUES</li><li>TESTIMONIALS</li><li>SOCIAL MEDIA</li><li>NEWS ALERT</li>
  </ul>
  <h1 class="abs hero-title">BRIGHT HARBOR VENTURE</h1>
  <p class="abs hero-text">Lorem ipsum dolor sit amet, consectetur adipiscing Sed ut perspiciatis unde sed do eiusmod tempor incididunt ut labore</p>
  <div class="abs dots"><i class="on"></i><i></i><i></i></div>
</header>

<section>
  <div class="abs services"></div>
  <h2 class="abs section-title" style="top:646px">OUR SERVICES</h2>
  <div class="abs card" style="left:98px">
    <div class="photo" role="img" aria-label="Two consultants reviewing a tablet" style="background:linear-gradient(135deg,#cfdce8,#5e7d9c)"></div>
    <h3>CONSULTANCY</h3>
    <ul><li>Professional and Personal</li><li>Next Generation Leaders (16-30)</li><li>Consultation Options</li></ul>
    <span class="btn-outline">Learn More</span>
  </div>
  <div class="abs card" style="left:445px">
    <div class="photo" role="img" aria-label="Team meeting around a presentation board" style="background:linear-gradient(135deg,#e6eef3,#8fb3cf)"></div>
    <h3>ON ASSIGNMENT</h3>
    <ul><li>Team Cohesion Strategy</li><li>Go To Market Strategy</li><li>Internationalisation Strategy</li></ul>
    <span class="btn-outline">Learn More</span>
  </div>
  <div class="abs card" style="left:790px">
    <div class="photo" role="img" aria-label="Couple meeting an agent outside a house" style="background:linear-gradient(135deg,#b9cfe0,#7c9a6a)"></div>
    <h3>PROPERTY: PRIVATE CLIENT</h3>
    <ul><li>Promotion and cash-buyer matching</li><li>Investment: high return projects</li><li>Commercial: Hotels and Senior Housing</li></ul>
    <span class="btn-outline">Learn More</span>
  </div>
</section>

<section>
  <div class="abs welcome"></div>
  <div class="abs video" role="img" aria-label="Video still of colleagues working at a laptop"></div>
  <div class="abs play"></div>
  <h2 class="abs welcome-title">WELCOME TO BRIGHT HARBOR VENTURE</h2>
  <div class="abs welcome-text">
    <p>If you seek an experienced and trusted partner to work with you on an assignment or simply want some strategies to move your personal or professional talents to the next level then you are in the right place. If you feel that the pace of change in business is so fast that to be an outstanding leader you should ensure you are brought up to speed regularly then you are in the right place.</p>
    <p>If you are hearing about the essential new leadership essentials and you are ready to hear how to adopt them into your life or business then you are at the right place.</p>
  </div>
  <div class="abs btn-dark">MORE VIDEOS ›</div>
</section>

<section>
  <h2 class="abs blog-title">LATEST BLOG</h2>
  <div class="abs arrows">←→</div>
  <article class="abs post" style="left:98px;top:1704px">
    <div class="thumb" role="img" aria-label="Laptop and charts on a desk" style="background:linear-gradient(135deg,#f1e4e6,#9fb6cf)"></div>
  </article>
  <article class="abs post" style="left:311px;top:1700px">
    <h4>Sed ut perspiciatis unde omnis iste natus Fehler sit voluptatem</h4>
    <p class="date">25, JUNI 2016</p>
    <p class="excerpt">Nulla bei diam ornare, aliquam urna vel, mmodo urna. Nam id risus ein est luctus consectetur quis eget libero. Suspendisse potenti.</p>
    <p class="more">Weiterlesen +</p>
  </article>
  <article class="abs post" style="left:634px;top:1704px">
    <div class="thumb" role="img" aria-label="Businesswoman smiling in a bright office" style="background:linear-gradient(135deg,#f3efe9,#c9c2b8)"></div>
  </article>
  <article class="abs post" style="left:846px;top:1700px">
    <h4>Sed ut perspiciatis unde omnis iste natus Fehler sit voluptatem</h4>
    <p class="date">25, JUNI 2016</p>
    <p class="excerpt">Nulla bei diam ornare, aliquam urna vel, mmodo urna. Nam id risus ein est luctus consectetur quis eget libero. Suspendisse potenti.</p>
    <p class="more">Weiterlesen +</p>
  </article>
</section>

<section>
  <div class="abs testimonials" role="img" aria-label="City skyline at dusk"></div>
  <h2 class="abs section-title testi-title">TESTIMONIALS</h2>
  <div class="abs quote-mark">“</div>
  <p class="abs quote">Lorem ipsum dolor sit amet, consectetur adipiscing elit, sed do eiusmod tempor incididunt ut labore et dolore magna aliqua. Ut enim ad minim veniam, quis nostrud exercitation ullamco laboris nisi ut aliquip ex ea commodo consequat. Duis aute irure dolor in reprehenderit in voluptate velit esse cillum dolore eu fugiat nulla Sed ut perspiciatis unde omnis iste natus error sit voluptatem accusantium doloremque laudantium, totam rem aperiam, eaque ipsa quae ab illo inventore veritatis et quasi architecto beatae vitae</p>
  <p class="abs author">John Doe - <small>Bright Harbor Venture</small></p>
  <div class="abs bars"><i class="on"></i><i></i><i></i></div>
</section>

<footer>
  <div class="abs footer"></div>
  <h3 class="abs foot-h" style="left:98px">SIGN UP FOR NEWSLETTER</h3>
  <p class="abs news-text">Excepteur sint occaecat cupidatat non proident, sunt in culpa qui officia deserunt</p>
  <div class="abs email-field">Enter email</div>
  <div class="abs subscribe">SUBSCRIPTION</div>

  <h3 class="abs foot-h" style="left:420px">CONTACTS US</h3>
  <div class="abs contact" style="top:2362px">
    <svg width="14" height="18" viewBox="0 0 14 18"><path d="M7 1a5.5 5.5 0 0 0-5.5 5.5C1.5 11 7 17 7 17s5.5-6 5.5-10.5A5.5 5.5 0 0 0 7 1z" fill="none" stroke="#55555c" stroke-width="1.5"/><circle cx="7" cy="6.5" r="2" fill="#55555c"/></svg>
    Bright Harbor Venture, New South Wales<br>Registeres number 10482915
  </div>
  <div class="abs contact" style="top:2419px">
    <svg width="14" height="14" viewBox="0 0 14 14"><path d="M3 1l2.5 3-1.5 1.5a8 8 0 0 0 4.5 4.5L10 8.5l3 2.5-1.5 2A11 11 0 0 1 1 2.5z" fill="#55555c"/></svg>
    Phone: +44 (0) 768 213 5597
  </div>
  <div class="abs contact" style="top:2450px">
    <svg width="14" height="12" viewBox="0 0 14 12"><rect x="1" y="2" width="12" height="9" fill="none" stroke="#55555c" stroke-width="1.5"/><path d="M1 2l6 5 6-5" fill="none" stroke="#55555c" stroke-width="1.5"/></svg>
    director@brightharborventure.com
  </div>

  <h3 class="abs foot-h" style="left:729px">QUICK LINKS</h3>
  <ul class="abs links">
    <li>Home</li><li>About Us</li><li>Our Values</li><li>Testimonials</li><li>Social Media</li><li>News Alert</li>
  </ul>

  <div class="abs foot-brand">BRIGHT HARBOR<br>VENTURE</div>
  <div class="abs socials" aria-label="Social media links">
    <span><svg width="14" height="14" viewBox="0 0 14 14"><path d="M2 3h10v6H6l-3 3V9H2z" fill="none" stroke="#55555c" stroke-width="1.4" stroke-linejoin="round"/></svg></span>
    <span><svg width="14" height="14" viewBox="0 0 14 14"><circle cx="3.5" cy="7" r="1.8" fill="#55555c"/><circle cx="10.5" cy="3" r="1.8" fill="#55555c"/><circle cx="10.5" cy="11" r="1.8" fill="#55555c"/><path d="M3.5 7l7-4M3.5 7l7 4" stroke="#55555c" stroke-width="1.2"/></svg></span>
    <span><svg width="14" height="14" viewBox="0 0 14 14"><path d="M6 8l2-2M5 6.5L3.5 8a2 2 0 0 0 2.8 2.8L7.8 9.3M9 7.5l1.5-1.5a2 2 0 0 0-2.8-2.8L6.2 4.7" fill="none" stroke="#55555c" stroke-width="1.4" stroke-linecap="round"/></svg></span>
    <span><svg width="14" height="12" viewBox="0 0 14 12"><rect x="1.5" y="2" width="11" height="8" fill="none" stroke="#55555c" stroke-width="1.3"/><path d="M1.5 2l5.5 4.5L12.5 2" fill="none" stroke="#55555c" stroke-width="1.3"/></svg></span>
  </div>

  <div class="abs bottom">©2015 - 2016 Bright Harbor Venture, All Rights Reserved.</div>
</footer>

</body>
</html>
```